Initial website for sport tech startup

We are currently in the R&D phases of our new product. It’s a headband to prevent concussion in the soccer market initially.

We have 2 products, one that’s basic aimed at the youth market and the other more technology driven that’s aimed at the academies and professional market.

Initially the product will launch in the UK

Target Market(s)

Youth soccer players and parents in UK, Soccer Clubs, Federations.

Industry/Entity Type

Sporting Good

Coding

Coded - Design and coding required

Number of Pages Required

5+ page

Requirements
Must have
• Professional style that can be adapted and changed over the coming months.
Nice to have
• Ecommerce ability in the future.

```html
<!DOCTYPE html>
<html lang="en">
<head>
<meta charset="utf-8">
<title>Helmora – Bringing Safety to the Sports</title>
<link href="https://fonts.googleapis.com/css2?family=Montserrat:wght@400;500;600;700;800&family=Open+Sans:wght@400;600&display=swap" rel="stylesheet">
<style>
:root{
  --blue:#2a8fdb;
  --blue-light:#4fc2ee;
  --blue-pale:#8fd9f3;
  --blue-deep:#1566c0;
  --ink:#1b1b1b;
  --text:#555;
  --grey-bg:#f1f1f1;
  --card-line:#d6d6d6;
  --footer:#333333;
  --white:#ffffff;
  --dark-photo:#0f1720;
}
*{box-sizing:border-box;margin:0;padding:0}
html,body{width:1200px;height:3871px;overflow:hidden}
body{position:relative;font-family:"Open Sans",Arial,sans-serif;color:var(--text);background:var(--white)}
.abs{position:absolute}
.heading{font-family:"Montserrat",Arial,sans-serif;font-weight:700;color:var(--ink);text-transform:uppercase}
.btn{position:absolute;display:flex;align-items:center;justify-content:center;font-family:"Montserrat",Arial,sans-serif;font-weight:700;font-size:15px;text-transform:uppercase;text-decoration:none}
.btn-solid{background:var(--blue);color:var(--white)}
.btn-outline-blue{border:2px solid var(--blue);color:var(--blue)}
.btn-outline-white{border:2px solid var(--white);color:var(--white)}

/* Hero */
.hero{left:0;top:0;width:1200px;height:800px}
.hero-photo{left:0;top:0;width:1200px;height:700px;background:radial-gradient(ellipse at 88% 40%,#f3c46a 0%,#a4682c 14%,#3b2e2a 35%,#121418 60%),linear-gradient(#0d0f12,#1c2a18);}
.hero-photo::after{content:"";position:absolute;left:0;right:0;bottom:0;height:190px;background:linear-gradient(180deg,rgba(40,90,30,0),#3f8a2c 70%,#5aa53a)}
.logo{left:87px;top:23px;width:249px;height:57px;border:3px solid var(--blue);display:flex;align-items:center;justify-content:center;font-family:"Montserrat",Arial,sans-serif;font-weight:500;font-size:36px;letter-spacing:2px;color:var(--white)}
.nav{left:428px;top:40px;display:flex;gap:34px}
.nav a{font-family:"Montserrat",Arial,sans-serif;font-weight:700;font-size:15px;color:var(--white);text-decoration:none}
.nav a.active{color:var(--blue)}
.hero-title{left:91px;top:258px;font-size:45px;line-height:54px;font-weight:800;color:var(--white)}
.hero-title span{color:var(--blue)}
.hero-text{left:97px;top:372px;width:430px;font-size:16px;line-height:27px;color:#e9e9e9}
.dots{left:1133px;top:311px;display:flex;flex-direction:column;gap:9px}
.dots i{display:block;width:14px;height:14px;border-radius:50%;background:var(--white)}
.dots i.on{background:transparent;border:2px solid var(--white)}

/* Mission */
.mission-title{left:0;width:1200px;top:822px;text-align:center;font-size:33px}
.mission-sub{left:0;width:1200px;top:873px;text-align:center;font-family:"Montserrat",Arial,sans-serif;font-weight:700;font-size:20px;line-height:28px;color:var(--blue);text-transform:uppercase}
.mission-text{left:150px;width:900px;top:941px;text-align:center;font-size:15px;line-height:27px}

/* Headband */
.headband{left:0;top:1190px;width:1200px;height:600px}
.headband-title{left:135px;top:1340px;font-size:31px;color:var(--white)}
.headband-text{left:135px;top:1394px;width:395px;font-size:15px;line-height:27px;color:#eef7fd}
.product{border-radius:40px 60px 30px 90px;background:linear-gradient(135deg,#5c6168,#34383e);box-shadow:0 18px 30px rgba(0,0,0,.35)}

/* Cards */
.cards{left:0;top:1784px;width:1200px;height:340px;background:var(--grey-bg)}
.card{position:absolute;top:1875px;width:295px;height:176px;background:var(--white);border:1px solid var(--card-line);text-align:center;padding-top:54px;font-family:"Montserrat",Arial,sans-serif;font-weight:600;font-size:16px;line-height:23px;color:#666}
.card-icon{position:absolute;top:1828px;width:94px;height:94px;border-radius:50%;display:flex;align-items:center;justify-content:center}

/* Background */
.bg-photo{left:0;top:2150px;width:720px;height:520px;background:linear-gradient(120deg,#3a4a30 0%,#6f7a78 35%,#c9ccd2 55%,#2a3a3a 100%)}
.bg-title{left:656px;top:2250px;font-size:31px;color:var(--white)}
.bg-sub{left:656px;top:2297px;font-family:"Montserrat",Arial,sans-serif;font-weight:700;font-size:16px;color:var(--white);text-transform:uppercase}
.bg-text{left:657px;top:2332px;width:440px;font-size:15px;line-height:25px;color:#e2e2e2}

/* Features */
.features-title{left:0;width:1200px;top:2738px;text-align:center;font-size:28px}
.feature{position:absolute;display:flex;align-items:center;gap:18px;font-family:"Montserrat",Arial,sans-serif;font-weight:500;font-size:18px;line-height:27px;color:#222}
.feature.right-align{text-align:right}

/* Quote */
.quote-mark{left:0;width:1200px;top:3370px;text-align:center;font-family:"Montserrat",Arial,sans-serif;font-weight:800;font-size:90px;line-height:90px;color:var(--white)}
.quote-text{left:200px;width:800px;top:3445px;text-align:center;font-size:18px;line-height:28px;color:#e4f2fc}
.quote-name{left:0;width:1200px;top:3540px;text-align:center;font-family:"Montserrat",Arial,sans-serif;font-weight:700;font-size:17px;color:var(--white)}
.quote-org{left:0;width:1200px;top:3570px;text-align:center;font-family:"Montserrat",Arial,sans-serif;font-weight:700;font-size:12px;color:var(--white)}

/* Footer */
.footer{left:0;top:3669px;width:1200px;height:202px;background:var(--footer)}
.footer-nav{left:0;width:1200px;top:3715px;display:flex;justify-content:center;gap:34px}
.footer-nav a{font-family:"Montserrat",Arial,sans-serif;font-weight:700;font-size:15px;color:var(--white);text-decoration:none}
.copyright{left:0;width:1200px;top:3755px;text-align:center;font-family:"Montserrat",Arial,sans-serif;font-size:13px;color:#ccc}
.social{left:0;width:1200px;top:3796px;display:flex;justify-content:center;gap:6px}
.social i{display:block;width:33px;height:33px;border-radius:50%;border:1.5px solid #ddd}
</style>
</head>
<body>

<!-- Hero -->
<section class="abs hero">
  <div class="abs hero-photo" role="img" aria-label="Two footballers contesting the ball in a floodlit stadium at sunset"></div>
  <svg class="abs" style="left:0;top:670px" width="1200" height="130" viewBox="0 0 1200 130">
    <polygon points="0,6 700,40 1200,30 1200,130 0,130" fill="var(--blue-light)"/>
    <polygon points="0,126 1200,12 1200,130 0,130" fill="var(--white)"/>
  </svg>
  <div class="abs logo">HELMORA</div>
  <nav class="abs nav">
    <a class="active" href="#">Home</a><a href="#">About Us</a><a href="#">Headband</a><a href="#">Features</a><a href="#">Resources</a><a href="#">Contact</a>
  </nav>
  <h1 class="abs heading hero-title">Bringing Safety<br><span>To The Sports</span></h1>
  <p class="abs hero-text">Helmora is designing and developing head protection products to reduce the likelihood</p>
  <a class="btn btn-solid" style="left:98px;top:448px;width:185px;height:54px" href="#">Learn More</a>
  <div class="abs dots"><i class="on"></i><i></i><i></i><i></i></div>
</section>

<!-- Mission -->
<h2 class="abs heading mission-title">Our Mission</h2>
<p class="abs mission-sub">Helmora – Bringing Safety to the Sports<br>Concussion Debate</p>
<p class="abs mission-text">Helmora is designing and developing head protection products to reduce the likelihood of concussion when playing sports. Exploring and understanding medical insights, material science and composites research, current and former players experiences and governing bodies guidelines has allowed Helmora to develop the safety, style, form and function requirements of a suitable product to bring to market in Q4 2020.</p>
<a class="btn btn-outline-blue" style="left:509px;top:1083px;width:176px;height:51px" href="#">Learn More</a>

<!-- Headband -->
<svg class="abs headband" width="1200" height="600" viewBox="0 0 1200 600">
  <defs>
    <linearGradient id="hbGrad" x1="0" y1="0" x2="1" y2="0">
      <stop offset="0" stop-color="#55c3ee"/><stop offset="0.55" stop-color="#2a8fdb"/><stop offset="1" stop-color="#1462bd"/>
    </linearGradient>
  </defs>
  <polygon points="0,12 1200,0 1200,594 0,594" fill="url(#hbGrad)"/>
  <polygon points="600,10 1200,0 1200,50" fill="var(--blue-light)"/>
  <polygon points="0,520 700,560 0,594" fill="var(--blue-deep)"/>
</svg>
<h2 class="abs heading headband-title">Our Head Band</h2>
<p class="abs headband-text">Augiat in pede Fusce tellus Sed metus augue convallis et vehicula ut pulvinar eu ante Integer orci tellus tristique vitae consequat nec mauris viverra in gravida eu mattis in ante Morbi eget arcurmentum vel congue id euismod in elit Fusc</p>
<a class="btn btn-outline-white" style="left:135px;top:1558px;width:162px;height:47px;font-size:14px" href="#">Learn More</a>
<div class="abs product" style="left:570px;top:1355px;width:478px;height:280px;transform:rotate(-8deg)" role="img" aria-label="Dark grey padded protective headband"></div>

<!-- Cards -->
<section class="abs cards"></section>
<div class="card" style="left:122px">Functional &amp;<br>Protective headgear<br>that is appealing</div>
<div class="card" style="left:449px">Allowing for new<br>categories of data<br>capture and analytics</div>
<div class="card" style="left:777px">Working group to<br>carry out intial trials</div>
<div class="card-icon" style="left:220px;background:var(--blue)">
  <svg width="48" height="48" viewBox="0 0 48 48" fill="none" stroke="#fff" stroke-width="5" stroke-linecap="round"><circle cx="26" cy="9" r="5" fill="#fff" stroke="none"/><path d="M12 20h22M24 20l-6 12 10 8M18 32l-8 8"/></svg>
</div>
<div class="card-icon" style="left:547px;background:#555">
  <svg width="46" height="46" viewBox="0 0 46 46" fill="none" stroke="#fff" stroke-width="3"><rect x="8" y="8" width="24" height="30" rx="3"/><path d="M15 5h10v6H15zM13 20h14M13 27h8"/><circle cx="33" cy="34" r="7" fill="#555"/><path d="M29.5 34l2.5 2.5 4.5-5"/></svg>
</div>
<div class="card-icon" style="left:877px;background:var(--blue)">
  <svg width="54" height="40" viewBox="0 0 54 40" fill="none" stroke="#fff" stroke-width="2.5"><circle cx="27" cy="11" r="6"/><circle cx="13" cy="15" r="5"/><circle cx="41" cy="15" r="5"/><path d="M17 32c0-8 20-8 20 0zM4 34c0-7 14-7 14-2M50 34c0-7-14-7-14-2"/></svg>
</div>

<!-- Background -->
<svg class="abs" style="left:0;top:2115px" width="1200" height="640" viewBox="0 0 1200 640">
  <polygon points="0,40 1200,12 1200,545 0,560" fill="var(--dark-photo)"/>
  <polygon points="780,35 1200,0 1200,40" fill="var(--blue-light)"/>
  <polygon points="0,540 480,548 0,630" fill="var(--blue-light)"/>
</svg>
<div class="abs bg-photo" role="img" aria-label="Footballer bent over on the pitch while players gather around him" style="clip-path:polygon(0 0,100% 0,100% 100%,0 100%);-webkit-mask-image:linear-gradient(90deg,#000 70%,transparent)"></div>
<h2 class="abs heading bg-title">Background</h2>
<p class="abs bg-sub">Dangers of head injury</p>
<p class="abs bg-text">More and more conversations are being had about concussion as a result of sporting injuries; a debate is ongoing about concussion in football and how dangerous is heading the ball, the impact of better understanding concussion in males and females is now the subject of medical journal articles, isolating the impact</p>
<a class="btn btn-outline-white" style="left:662px;top:2502px;width:161px;height:47px;font-size:14px" href="#">Learn More</a>

<!-- Features -->
<h2 class="abs heading features-title">Our Features</h2>
<div class="abs product" style="left:478px;top:2960px;width:270px;height:150px;transform:rotate(-6deg)" role="img" aria-label="Dark grey padded protective headband"></div>

<div class="feature" style="right:698px;top:2842px">Safety tested
  <svg width="46" height="50" viewBox="0 0 46 50" fill="none" stroke="var(--blue)" stroke-width="3"><path d="M23 3l18 7v14c0 12-8 20-18 23C13 44 5 36 5 24V10z"/><circle cx="23" cy="25" r="9"/><path d="M19 25l3 3 6-6"/></svg>
</div>
<div class="feature" style="left:697px;top:2842px">
  <svg width="52" height="48" viewBox="0 0 52 48" fill="none" stroke="var(--blue)" stroke-width="3"><rect x="3" y="20" width="12" height="25"/><path d="M15 22l10-16c4 0 6 3 5 7l-2 7h16c3 0 5 3 4 6l-4 15c-1 3-3 4-6 4H15"/></svg>
  Comfortable</div>

<div class="feature" style="right:762px;top:2940px">Environmentally friendly
  <svg width="48" height="48" viewBox="0 0 48 48" fill="none" stroke="var(--blue)" stroke-width="3"><circle cx="24" cy="24" r="20"/><ellipse cx="24" cy="24" rx="9" ry="20"/><path d="M4 24h40M8 13h32M8 35h32"/></svg>
</div>
<div class="feature" style="left:800px;top:2940px">
  <svg width="42" height="52" viewBox="0 0 42 52"><path d="M21 2C14 16 5 24 5 34a16 16 0 0 0 32 0C37 24 28 16 21 2z" fill="var(--blue)"/><path d="M14 36a7 7 0 0 0 7 7" stroke="#fff" stroke-width="3" fill="none"/></svg>
  Washable, antibacterial fabric</div>

<div class="feature" style="right:776px;top:3044px">Available in a range of sizes
  <svg width="50" height="58" viewBox="0 0 50 58" fill="none" stroke="var(--blue)" stroke-width="3"><rect x="4" y="8" width="34" height="44" rx="3"/><path d="M14 4h14v8H14zM11 24l3 3 5-5M23 25h10M11 36l3 3 5-5M23 37h10"/><circle cx="39" cy="47" r="9" fill="var(--blue)" stroke="none"/><path d="M34.5 47l3 3 6-6" stroke="#fff"/></svg>
</div>
<div class="feature" style="left:788px;top:3044px">
  <svg width="60" height="44" viewBox="0 0 60 44"><path d="M2 40C12 36 20 22 40 10c8-5 14-7 18-8-2 8-8 20-18 28-10 7-22 10-32 10z" fill="var(--blue)"/><path d="M4 40L38 16" stroke="#fff" stroke-width="2"/></svg>
  Light-weight</div>

<div class="feature right-align" style="right:682px;top:3172px">charitable donation<br>will be made
  <svg width="56" height="56" viewBox="0 0 56 56" fill="none" stroke="var(--blue)" stroke-width="2.5"><path d="M6 22l12-12 10 6 10-6 12 12-10 10-12 12-12-12z"/><path d="M18 28l6 6M24 22l8 8M30 36l4 4"/></svg>
</div>
<div class="feature" style="left:697px;top:3168px">
  <svg width="60" height="64" viewBox="0 0 60 64" fill="none" stroke="var(--blue)" stroke-width="2.5"><path d="M30 8c-12 0-20 8-20 18 0 7 4 11 8 14v8h24v-8c4-3 8-7 8-14 0-10-8-18-20-18z"/><path d="M22 54h16M25 60h10M30 14v26M22 22c4 0 8 3 8 6M38 22c-4 0-8 3-8 6"/><path d="M4 10l4 2M56 10l-4 2M8 2l3 4M52 2l-3 4"/></svg>
  A second product<br>incorporating</div>

<!-- Quote -->
<svg class="abs" style="left:0;top:3255px" width="1200" height="420" viewBox="0 0 1200 420">
  <polygon points="0,44 1200,72 1200,420 0,420" fill="var(--blue)"/>
  <polygon points="660,44 1200,0 1200,72" fill="var(--blue-pale)"/>
</svg>
<div class="abs quote-mark">“</div>
<p class="abs quote-text">We are seeing more and more children come to matches with home-made head protection. In addition, we are having more concern from parents about heading the ball and getting asked more about our guidelines on heading and head injuries</p>
<p class="abs quote-name">Chief Executive, County</p>
<p class="abs quote-org">Fieldside Football Association</p>
<svg class="abs" style="left:128px;top:3470px" width="24" height="36" viewBox="0 0 24 36"><path d="M20 3L5 18l15 15" stroke="#fff" stroke-width="4" fill="none"/></svg>
<svg class="abs" style="left:1046px;top:3470px" width="24" height="36" viewBox="0 0 24 36"><path d="M4 3l15 15L4 33" stroke="#fff" stroke-width="4" fill="none"/></svg>

<!-- Footer -->
<footer class="abs footer"></footer>
<nav class="abs footer-nav">
  <a href="#">Home</a><a href="#">About Us</a><a href="#">Headband</a><a href="#">Features</a><a href="#">Resources</a><a href="#">Contact</a>
</nav>
<p class="abs copyright">© 2020 Company Name | All Rights Reserved</p>
<div class="abs social"><i></i><i></i><i></i><i></i></div>

</body>
</html>
```